Trueline Referral Hub needs updated website.

Our current website was designed on wix.com. (www.truelinereferralhub.example).
We would like something a little more customized for what our company offers. Trueline Referral Hub is a company specializing in connecting consumers with trustworthy and affordable service professionals. We need the website to be approachable and easy to use, while conveying our "Trueline" reputation.
Reason: Our project is now guaranteed. Please send your ideas. Thank you!
Target Market(s)
Homeowners
Industry/Entity Type
It Company
Look and feel
Each slider illustrates characteristics of the customer's brand and the style your logo design should communicate.

```html
<!DOCTYPE html>
<html lang="en">
<head>
<meta charset="utf-8">
<title>Trueline Referral Hub</title>
<link href="https://fonts.googleapis.com/css2?family=Open+Sans:wght@400;600;700&family=PT+Sans:wght@400;700&display=swap" rel="stylesheet">
<style>
:root{
  --green:#6aaa1f;
  --green-deep:#4a7e0b;
  --green-footer:#4d7f10;
  --green-soft:#8fc94a;
  --ink:#3a3a3a;
  --ink-soft:#555;
  --muted:#9a9a9a;
  --hero-bg:#e9eef2;
  --white:#fff;
  --line:#dcdcdc;
}
*{box-sizing:border-box;margin:0;padding:0}
html,body{width:717px;height:1200px;overflow:hidden;background:var(--white)}
body{position:relative;font-family:"Open Sans",Arial,sans-serif;color:var(--ink)}
.abs{position:absolute}

/* header */
.brand{left:63px;top:24px;display:flex;align-items:center;gap:8px}
.brand-dot{width:38px;height:38px;border-radius:50%;background:var(--green)}
.brand-name{font-family:"PT Sans",Arial,sans-serif;font-weight:700;font-size:21px;color:#555;line-height:1.05;width:130px}
.header-address{left:393px;top:26px;font-size:9.5px;line-height:13px;color:var(--ink-soft)}
.header-call{left:558px;top:27px;font-size:11px;color:var(--ink-soft)}
.header-call strong{display:block;font-size:14px;font-weight:700;color:#444;margin-top:2px;letter-spacing:.5px}
.header-rule{left:0;top:92px;width:717px;height:1px;background:var(--green-soft)}

/* nav */
.nav{left:0;top:93px;width:717px;height:40px}
.nav a{position:absolute;top:0;height:40px;line-height:38px;font-size:12.5px;color:#333;text-decoration:none;text-transform:uppercase}
.nav a.active{background:var(--green);color:var(--white);font-weight:700;text-align:center;width:100px;left:63px;border-bottom:2px solid var(--white);box-shadow:0 2px 0 var(--green)}

/* hero */
.hero{left:0;top:133px;width:717px;height:268px;background:linear-gradient(90deg,#eef2f5 0%,#e6ecf0 55%,#f3f6f8 100%)}
.hero-photo{left:330px;top:133px;width:387px;height:268px;background:linear-gradient(90deg,rgba(230,236,240,0) 0%,#d9c3ad 25%,#e7d3c0 55%,#b9cde0 80%,#eef2f5 100%)}
.hero-title{left:61px;top:166px;font-size:31px;line-height:37px;letter-spacing:1.5px;color:#3e4246;text-transform:uppercase;font-weight:400}
.hero-title em{font-style:normal;font-weight:700;color:var(--green)}
.hero-text{left:62px;top:285px;font-size:10.5px;line-height:15px;color:#444;width:300px}
.hero-link{left:62px;top:324px;font-size:10px;color:#444;text-transform:uppercase}
.hero-dots{left:61px;top:364px;display:flex;gap:4px}
.hero-dots span{width:10px;height:10px;border-radius:50%;background:#b8bcc0}
.hero-dots span.on{background:var(--green)}

/* intro */
.intro-title{left:0;top:414px;width:717px;text-align:center;font-size:20px;font-weight:700;color:var(--green)}
.intro-text{left:0;top:446px;width:717px;text-align:center;font-size:7.5px;color:#444}

/* services band */
.services{left:0;top:474px;width:717px;height:293px;background:var(--green-deep)}
.service-card--active{left:101px;top:474px;width:164px;height:293px;background:var(--white)}
.service{top:500px;width:142px}
.service h3{font-size:11px;font-weight:700;color:var(--white);text-transform:uppercase;height:24px}
.service .thumb{width:138px;height:104px;margin-top:0}
.service p{font-size:7.4px;line-height:10px;color:var(--white);margin-top:16px}
.service .more{display:block;font-size:7.5px;font-weight:700;color:var(--white);margin-top:11px;text-transform:uppercase}
.service.active h3,.service.active p{color:var(--green)}
.service.active .more{color:var(--green-deep)}
.arrow{top:605px;width:29px;height:34px;background:var(--white)}
.arrow svg{display:block;margin:9px auto 0}

/* about */
.about-title{left:62px;top:782px;font-family:"PT Sans",Arial,sans-serif;font-size:29px;font-weight:700;color:var(--green-deep)}
.about-lead{left:62px;top:824px;font-family:"PT Sans",Arial,sans-serif;font-size:17px;line-height:22px;color:#333}
.about-lead span{color:var(--green)}
.about-text{left:62px;top:886px;width:360px;font-family:"PT Sans",Arial,sans-serif;font-size:12.3px;line-height:16.5px;color:#333}
.btn{left:62px;top:1011px;width:85px;height:31px;line-height:31px;background:var(--green-deep);color:var(--white);text-align:center;font-family:"PT Sans",Arial,sans-serif;font-size:12.5px;text-decoration:none}
.about-divider{left:440px;top:783px;width:1px;height:262px;background:var(--line)}

/* offer */
.offer-title{left:487px;top:783px;font-family:"PT Sans",Arial,sans-serif;font-size:21px;font-weight:700;color:var(--green-deep)}
.offer{left:488px;width:200px;height:57px}
.offer .thumb{position:absolute;left:0;top:0;width:56px;height:56px}
.offer h4{position:absolute;left:62px;top:1px;font-size:7.6px;font-weight:400;color:var(--green);text-transform:uppercase;white-space:nowrap}
.offer p{position:absolute;left:62px;top:15px;font-size:7px;line-height:10.5px;color:var(--muted);width:115px}

/* footer */
.footer{left:0;top:1061px;width:717px;height:139px;background:var(--green-footer);color:var(--white)}
.footer-brand{left:63px;top:1089px;display:flex;align-items:center;gap:6px}
.footer-brand .brand-dot{width:28px;height:28px;background:var(--white)}
.footer-brand .brand-name{color:var(--white);font-size:15px;width:auto}
.copyright{left:63px;top:1131px;font-size:7.5px;color:var(--white)}
.footer-nav{right:63px;top:1082px;display:flex;gap:14px;font-size:7.8px}
.footer-nav a{color:var(--white);text-decoration:none}
.footer-address{right:63px;top:1111px;font-size:10.5px;text-align:right}
.footer-phone{right:63px;top:1135px;font-size:13.5px;color:#a9dc5c;text-align:right}
.footer-email{right:63px;top:1153px;font-size:11px;text-align:right}
</style>
</head>
<body>

<header>
  <div class="abs brand"><span class="brand-dot"></span><span class="brand-name">Trueline Referral Hub</span></div>
  <div class="abs header-address">418 Harmon Street, Saint<br>Louis, Missouri 63199<br><span style="display:block;margin-top:4px">E-mail: info@truelinereferralhub.example</span></div>
  <div class="abs header-call">Call Us Now:<strong>1 555 014 2207</strong></div>
  <div class="abs header-rule"></div>
  <nav class="abs nav">
    <a class="active" href="#">Home</a>
    <a href="#" style="left:205px">About Trueline</a>
    <a href="#" style="left:357px">Services</a>
    <a href="#" style="left:455px">Our Network</a>
    <a href="#" style="left:584px">Contact Us</a>
  </nav>
</header>

<section>
  <div class="abs hero"></div>
  <div class="abs hero-photo" role="img" aria-label="Two smiling support agents wearing headsets"></div>
  <h1 class="abs hero-title">Sometimes all<br>you really need<br><em>is a Trueline</em></h1>
  <p class="abs hero-text">Praesent vestibulum aenean nonummy hendrerit mauris. Hasellus porta. Fusce suscipit varius mi cum sociis</p>
  <a class="abs hero-link">Learn more →</a>
  <div class="abs hero-dots"><span class="on"></span><span></span><span></span><span></span></div>
</section>

<section>
  <h2 class="abs intro-title">TRUELINE REFERRAL HUB</h2>
  <p class="abs intro-text">Praesent vestibulum aenean nonummy hendrerit mauris. Hasellus porta. Fusce suscipit varius mi cum sociis natoque penatibus et magnis.</p>

  <div class="abs services"></div>
  <div class="abs service-card--active"></div>

  <div class="abs arrow" style="left:62px"><svg width="10" height="16" viewBox="0 0 10 16"><path d="M8 2 2 8l6 6" fill="none" stroke="#4a7e0b" stroke-width="3"/></svg></div>
  <div class="abs arrow" style="left:626px"><svg width="10" height="16" viewBox="0 0 10 16"><path d="M2 2l6 6-6 6" fill="none" stroke="#4a7e0b" stroke-width="3"/></svg></div>

  <article class="abs service active" style="left:115px">
    <h3>Heating</h3>
    <div class="thumb" role="img" aria-label="Empty wooden-floored room with a heater" style="background:linear-gradient(180deg,#8a4e2e 0%,#b98f73 35%,#d9d7d2 70%,#c7c6c2 100%)"></div>
    <p>Praesent vestibulum aenean nonummy hendrerit mauris. Hasellus porta. Fusce suscipit varius mi cum sociis natoque penatibus et magnis dis parturient montes nascetur. sociis natoque penati-bus et magnis dis parturient montes nascetur.</p>
    <span class="more">Read more</span>
  </article>
  <article class="abs service" style="left:287px">
    <h3>Air Conditioning</h3>
    <div class="thumb" role="img" aria-label="Outdoor air conditioning unit under a blue sky" style="background:linear-gradient(90deg,#d8dadb 0%,#c4c6c8 50%,#6d9dd6 80%,#9bbfe8 100%)"></div>
    <p>Praesent vestibulum aenean nonummy hendrerit mauris. Hasellus porta. Fusce suscipit varius mi cum sociis natoque penatibus et magnis dis parturient montes nascetur. sociis natoque penati-bus et magnis dis parturient montes nascetur.</p>
    <span class="more">Read more</span>
  </article>
  <article class="abs service" style="left:459px">
    <h3>Automotive Maintence</h3>
    <div class="thumb" role="img" aria-label="Set of chrome wrenches and tools" style="background:linear-gradient(135deg,#2f3f7c 0%,#9aa4b8 40%,#e0e3e8 60%,#3b4b85 100%)"></div>
    <p>Praesent vestibulum aenean nonummy hendrerit mauris. Hasellus porta. Fusce suscipit varius mi cum sociis natoque penatibus et magnis dis parturient montes nascetur. sociis natoque penati-bus et magnis dis parturient montes nascetur.</p>
    <span class="more">Read more</span>
  </article>
</section>

<section>
  <h2 class="abs about-title">Trueline Referral Hub</h2>
  <p class="abs about-lead"><span>Connecting YOU</span> with the most reputable<br>and affordable businesses in Saint Louis.</p>
  <p class="abs about-text">The founders of Trueline Referral Hub have over 30 years in the St. Louis Automotive and HVAC industries. In both markets, among many others, one thing is clear: A consumer gets better service at a lower price when they know who to call.  Opening up a phonebook, newspa-per, or randomly selected online business could cost you hundreds, even thousands of dollars too much money.</p>
  <a class="abs btn" href="#">Know More</a>
  <div class="abs about-divider"></div>

  <h2 class="abs offer-title">WE OFFER</h2>
  <div class="abs offer" style="top:827px">
    <div class="thumb" role="img" aria-label="Portrait of a businessman in a suit" style="background:linear-gradient(180deg,#e8ecef,#c9cfd6 60%,#3d3f45)"></div>
    <h4>Call Answering Services</h4>
    <p>Accusamu dolore masugharum quidemed rerum facilis iustossi mos ducimus qui blanditiistes</p>
  </div>
  <div class="abs offer" style="top:906px">
    <div class="thumb" role="img" aria-label="Person raising arms against a bright sky" style="background:linear-gradient(180deg,#dce9f4,#eef4f8 55%,#7f8a94)"></div>
    <h4>24/7 Support Services</h4>
    <p>Accusamu dolore masugharum quidemed rerum facilis iustossi mos ducimus qui blanditiistes</p>
  </div>
  <div class="abs offer" style="top:985px">
    <div class="thumb" role="img" aria-label="Smiling woman holding a cup" style="background:linear-gradient(180deg,#f1f3f5,#e3d6c6 55%,#c9d8e6)"></div>
    <h4>Network Management</h4>
    <p>Accusamu dolore masugharum quidemed rerum facilis iustossi mos ducimus qui blanditiistes</p>
  </div>
</section>

<footer>
  <div class="abs footer"></div>
  <div class="abs footer-brand"><span class="brand-dot"></span><span class="brand-name">Trueline Referral Hub</span></div>
  <p class="abs copyright">© copyrights Trueline Referral Hub Inc. All rights reserved</p>
  <nav class="abs footer-nav"><a href="#">Home</a><a href="#">About trueline</a><a href="#">Services</a><a href="#">Our network</a><a href="#">Contact us</a></nav>
  <p class="abs footer-address">418 Harmon Street, Saint Louis, Missouri 63199</p>
  <p class="abs footer-phone">Phone: 1-555-014-2207</p>
  <p class="abs footer-email">E-mail: info@truelinereferralhub.example</p>
</footer>

</body>
</html>
```